New Year's card HTML

can you produce a best new years wishes 2018 design in HTML for our website as what I would like to send by email towards my network of candidates / customers ...

It must be wow, inspiring , design, meaningfull... MMM those people care about me, or those people will help me to go the extra mile, to help me to achieve my career goals, Your best move, enhance my possibilities, bring the love back

Target Market(s)

CEo's / CMO's/ HRDirectors network of 450k

Coding

Coded - Design and coding required

Number of Pages Required

1 page

Colors

Designer to choose colors to be used in the design.

Requirements
Must have
• Logo / visual / website adress www.moravintel.com and a call to action
Should not have
• no sound as our business is confidential

```html
<!DOCTYPE html>
<html lang="en">
<head>
<meta charset="UTF-8">
<title>Happy New Year 2018 – Moravintel</title>
<link rel="stylesheet" href="https://fonts.googleapis.com/css2?family=Comfortaa:wght@300&family=Cinzel:wght@400&family=Open+Sans:wght@700&display=swap">
<style>
  :root {
    --bg-deep: #0b0d1a;
    --bg-mid: #161a2e;
    --bg-warm: #2a1620;
    --neon-white: #f4f2f4;
    --neon-glow: rgba(255, 70, 70, 0.75);
    --globe-cyan: #5fe0e6;
    --globe-teal: #2a8fb0;
    --globe-blue: #2b3f8c;
    --globe-violet: #6a3f9e;
    --text-white: #ffffff;
  }
  * { margin: 0; padding: 0; box-sizing: border-box; }
  html, body {
    width: 1200px;
    height: 909px;
    overflow: hidden;
    background: var(--bg-deep);
  }
  .card {
    position: relative;
    width: 1200px;
    height: 909px;
    overflow: hidden;
    background: var(--bg-deep);
  }
  .card__backdrop {
    position: absolute;
    inset: 0;
    background:
      radial-gradient(ellipse 520px 260px at 180px 520px, rgba(120, 40, 60, 0.35), transparent 70%),
      radial-gradient(ellipse 700px 400px at 400px 300px, rgba(40, 46, 80, 0.55), transparent 75%),
      linear-gradient(180deg, var(--bg-mid) 0%, var(--bg-deep) 55%, var(--bg-warm) 100%);
  }
  .card__globe {
    position: absolute;
    left: 543px;
    top: 300px;
    width: 690px;
    height: 690px;
    border-radius: 50%;
    background:
      radial-gradient(circle at 35% 30%, rgba(150, 245, 250, 0.55), transparent 45%),
      radial-gradient(circle at 70% 80%, rgba(130, 70, 180, 0.7), transparent 55%),
      radial-gradient(circle at 50% 50%, var(--globe-teal) 0%, var(--globe-blue) 60%, var(--globe-violet) 100%);
    box-shadow: 0 0 60px rgba(95, 224, 230, 0.35);
  }
  .headline {
    position: absolute;
    left: 0;
    top: 0;
    width: 1200px;
    height: 420px;
  }
  .headline text {
    font-family: 'Comfortaa', sans-serif;
    font-weight: 300;
    fill: none;
    stroke: var(--neon-white);
    stroke-dasharray: 9 5;
    stroke-linecap: round;
    filter: drop-shadow(0 0 6px var(--neon-glow)) drop-shadow(0 0 14px var(--neon-glow));
  }
  .headline__greeting { font-size: 118px; stroke-width: 3; letter-spacing: 4px; }
  .headline__year { font-size: 200px; stroke-width: 4.5; letter-spacing: 6px; }
  .brand {
    position: absolute;
    left: 56px;
    top: 660px;
    display: flex;
    align-items: center;
    gap: 26px;
  }
  .brand__dot {
    width: 62px;
    height: 62px;
    border-radius: 50%;
    background: var(--text-white);
  }
  .brand__name {
    font-family: 'Cinzel', serif;
    font-weight: 400;
    font-size: 46px;
    letter-spacing: 1px;
    color: var(--text-white);
  }
  .cta {
    position: absolute;
    left: 54px;
    top: 767px;
    width: 220px;
    height: 65px;
    border: 2.5px solid var(--text-white);
    border-radius: 33px;
    display: flex;
    align-items: center;
    justify-content: center;
    font-family: 'Open Sans', sans-serif;
    font-weight: 700;
    font-size: 21px;
    color: var(--text-white);
    text-decoration: none;
  }
</style>
</head>
<body>
  <main class="card">
    <div class="card__backdrop" role="img" aria-label="Dark circuit board texture with faint binary code and red glowing traces"></div>
    <div class="card__globe" role="img" aria-label="Glowing digital globe wrapped in a triangular network mesh"></div>

    <svg class="headline" viewBox="0 0 1200 420" aria-label="Happy New Year 2018">
      <text class="headline__greeting" x="62" y="166">Happy New Year</text>
      <text class="headline__year" x="58" y="375">2018</text>
    </svg>

    <div class="brand">
      <span class="brand__dot"></span>
      <span class="brand__name">MORAVINTEL</span>
    </div>

    <a class="cta" href="https://www.moravintel.com">VISIT OUR SITE</a>
  </main>
</body>
</html>
```